Redesign of business card for Cedar Ridge Mechanical

We are looking for a new design for our business cards for Cedar Ridge Mechanical. We are a plumbing & HVAC construction company, operating on the West Coast of Canada and USA. Logo attached.
Industry/Entity Type
Construction - Plumbing & HVAC
Contact Information for Business Card
Name, address, phone numbers, email, website address
Look and feel
Each slider illustrates characteristics of the customer's brand and the style your logo design should communicate.

```html
<!DOCTYPE html>
<html lang="en">
<head>
<meta charset="UTF-8">
<title>Cedar Ridge Mechanical – Business Card</title>
<link href="https://fonts.googleapis.com/css2?family=Poppins:wght@300;400;600;700&display=swap" rel="stylesheet">
<style>
  :root {
    --backdrop: #222222;
    --card-black: #141414;
    --card-back: #161616;
    --ink-white: #ffffff;
    --ink-black: #111111;
    --emboss: #2e2e2e;
    --rule: #e8e8e8;
  }
  * { margin: 0; padding: 0; box-sizing: border-box; }
  html, body {
    width: 1200px; height: 780px; overflow: hidden;
    background: var(--backdrop);
    font-family: 'Poppins', sans-serif;
  }
  .canvas { position: relative; width: 1200px; height: 780px; }

  .card {
    position: absolute; top: 235px;
    width: 540px; height: 310px;
    border-radius: 4px; overflow: hidden;
  }
  .card--front { left: 45px; background: var(--card-black); }
  .card--back  { left: 615px; background: var(--card-back);
    display: flex; align-items: center; justify-content: center; }

  .card__swoosh { position: absolute; inset: 0; width: 540px; height: 310px; }

  .holder { position: absolute; left: 30px; top: 34px; color: var(--ink-white); }
  .holder__name { font-size: 27px; line-height: 1.1; }
  .holder__first { font-weight: 700; }
  .holder__last { font-weight: 300; }
  .holder__title { font-size: 12px; font-weight: 300; margin-top: 6px; padding-left: 60px; }

  .brand {
    position: absolute; left: 300px; top: 40px;
    display: flex; align-items: center; gap: 10px;
    color: var(--ink-white);
  }
  .brand__mark { width: 22px; height: 22px; border: 2px solid var(--ink-white); border-radius: 3px; }
  .brand__name { font-size: 15px; font-weight: 600; letter-spacing: 0.5px; }

  .divider {
    position: absolute; left: 270px; top: 112px;
    width: 1.5px; height: 78px; background: var(--rule);
  }

  .contact { position: absolute; left: 295px; top: 120px; list-style: none; color: var(--ink-white); }
  .contact__item { display: flex; align-items: center; gap: 10px; font-size: 14px; font-weight: 400; height: 24px; }
  .contact__icon { width: 14px; height: 14px; flex: none; }

  .address {
    position: absolute; left: 30px; top: 276px;
    font-size: 12.5px; font-weight: 400; color: var(--ink-black);
    white-space: nowrap;
  }

  .back__name {
    font-size: 30px; font-weight: 600; color: var(--emboss);
    display: flex; align-items: center; gap: 16px; letter-spacing: 1px;
  }
  .back__mark { width: 34px; height: 34px; border: 3px solid var(--emboss); border-radius: 5px; }
</style>
</head>
<body>
<main class="canvas">

  <section class="card card--front" aria-label="Business card front">
    <svg class="card__swoosh" viewBox="0 0 540 310" aria-hidden="true">
      <path d="M0,140 C120,218 330,250 540,250 L540,310 L0,310 Z" fill="#ffffff"/>
      <path d="M28,162 C140,232 330,262 530,262" fill="none" stroke="#111111" stroke-width="3" stroke-linecap="round"/>
    </svg>

    <div class="holder">
      <p class="holder__name"><span class="holder__first">Marta</span> <span class="holder__last">Kovalik</span></p>
      <p class="holder__title">Founder &amp; CEO</p>
    </div>

    <div class="brand">
      <span class="brand__mark"></span>
      <span class="brand__name">Cedar Ridge Mechanical</span>
    </div>

    <span class="divider"></span>

    <ul class="contact">
      <li class="contact__item">
        <svg class="contact__icon" viewBox="0 0 24 24"><path fill="#fff" d="M6.6 10.8a15.1 15.1 0 0 0 6.6 6.6l2.2-2.2a1 1 0 0 1 1-.25 11.4 11.4 0 0 0 3.6.57 1 1 0 0 1 1 1V20a1 1 0 0 1-1 1A17 17 0 0 1 3 4a1 1 0 0 1 1-1h3.5a1 1 0 0 1 1 1c0 1.250.2 2.45.57 3.57a1 1 0 0 1-.25 1z"/></svg>
        (604) 555-0147
      </li>
      <li class="contact__item">
        <svg class="contact__icon" viewBox="0 0 24 24"><circle cx="12" cy="12" r="9" fill="none" stroke="#fff" stroke-width="2"/><path d="M3 12h18M12 3c3 3 3 15 0 18M12 3c-3 3-3 15 0 18" fill="none" stroke="#fff" stroke-width="1.6"/></svg>
        info@cedarridgemech.com
      </li>
      <li class="contact__item">
        <svg class="contact__icon" viewBox="0 0 24 24"><rect x="2.5" y="5" width="19" height="14" rx="1.5" fill="none" stroke="#fff" stroke-width="2"/><path d="M3 6l9 7 9-7" fill="none" stroke="#fff" stroke-width="2"/></svg>
        www.cedarridgemech.com
      </li>
    </ul>

    <p class="address">1840 Harbour Rd. Suite 310 Vancouver, BC V6B 2K4</p>
  </section>

  <section class="card card--back" aria-label="Business card back">
    <p class="back__name"><span class="back__mark"></span>Cedar Ridge Mechanical</p>
  </section>

</main>
</body>
</html>
```